Business Card Design - Photographer

I am a landscape photographer and I require a business card design. 

I require two designs:
1)  a double sided business card
 and
b)  a single sided business card 

The single sided design can either be the same as the double sided (with just one side having all the information)....or it can be an entire new design. Its up to you.

My corporate colours are (CMYK):

Blue   69, 32, 0, 0
Grey  72,  64,  47,  31
Green  32,  2,  91,  0
Yellow   0, 19, 92, 0
Orange  0, 39, 75, 0

Colour space in final file should be in CMYK.

The details that need to be included on the card:

- Use the provided Logo
- Name: Wiktor Baranowski
- Email:   sales@vistalumeworks.com.au
- Website:    vistalumeworks.com.au
- Twitter:    twitter.com/vistalumeworks
- Facebook:   facebook.com/vistalumeworks
- Mobile  0417 539 662

Please use the attached template to design the logo to the specified size, including the marked bleed lines. I have also attached my logo in PNG (transparent background) and ai format for you to use.

The final file should be:
- Photoshop version with layers so I can edit the name/text etc. All non vector files should be high resolution at 1039 x 697 pixels at 300 dpi.

I also require a file as:
- Vector based PDF

Anyway questions please contact me.

Thank you

Industry/Entity Type

Landscape

Logo styles of interest
Pictorial/Combination Logo
Abstract Logo
Wordmark Logo
Lettermark Logo
Requirements
Must have
• The details that need to be included on the card:

- Use the provided Logo
- Name: Wiktor Baranowski
- Email: sales@vistalumeworks.com.au
- Website: vistalumeworks.com.au
- Twitter: twitter.com/vistalumeworks
- Facebook: facebook.com/vistalumeworks
- Mobile 0417 539 662

```html
<!DOCTYPE html>
<html lang="en">
<head>
<meta charset="utf-8">
<title>Vistalume Works – Business Cards</title>
<link rel="stylesheet" href="https://fonts.googleapis.com/css2?family=Cinzel:wght@400;600;700&display=swap">
<style>
  :root {
    --backdrop: #808184;
    --card: #ffffff;
    --slate: #3d3f51;
    --sun: #fdc70c;
    --sky: #3f8fd0;
    --leaf: #b5d33c;
    --ember: #f7a449;
    --white: #ffffff;
  }
  * { margin: 0; padding: 0; box-sizing: border-box; }
  html, body {
    width: 976px; height: 1200px; overflow: hidden;
    background: var(--backdrop);
    font-family: "Cinzel", "Trajan Pro", serif;
    color: var(--slate);
  }
  .sheet { position: relative; width: 976px; height: 1200px; }
  .card {
    position: absolute;
    width: 820px; height: 466px;
    background: var(--card);
    border-radius: 30px;
    overflow: hidden;
    box-shadow: 3px 4px 6px rgba(0,0,0,0.45);
  }
  .card--front { left: 70px; top: 88px; }
  .card--back  { left: 74px; top: 647px; }
  .card__bands { position: absolute; inset: 0; width: 820px; height: 466px; }
  .band--sun { fill: var(--sun); }
  .band--slate { fill: var(--slate); }

  .brand { position: absolute; text-align: center; }
  .brand__mark { border-radius: 50%; background: var(--slate); margin: 0 auto; }
  .brand__name {
    font-weight: 600; white-space: nowrap;
    color: var(--slate); line-height: 1;
  }
  .brand__rule { height: 2px; background: var(--slate); }
  .brand__tagline {
    font-weight: 700; white-space: nowrap; line-height: 1;
  }
  .card--front .brand { left: 43px; top: 122px; width: 494px; }
  .card--front .brand__mark { width: 170px; height: 170px; margin-left: 158px; }
  .card--front .brand__name { font-size: 47px; letter-spacing: 1.6px; margin-top: 36px; }
  .card--front .brand__rule { margin-top: 8px; }
  .card--front .brand__tagline { font-size: 18px; letter-spacing: 4.6px; margin-top: 14px; }

  .card--back .brand { left: 36px; top: 52px; width: 394px; }
  .card--back .brand__mark { width: 150px; height: 150px; margin-left: 122px; }
  .card--back .brand__name { font-size: 37px; letter-spacing: 1.2px; margin-top: 26px; }
  .card--back .brand__rule { margin-top: 7px; }
  .card--back .brand__tagline { font-size: 15.5px; letter-spacing: 4px; margin-top: 12px; }

  .contact { position: absolute; left: 56px; top: 318px; list-style: none; }
  .contact__item { font-size: 16.5px; line-height: 27.5px; letter-spacing: 0.9px; white-space: nowrap; }
  .contact__key { color: var(--sky); font-size: 19px; }
  .website {
    position: absolute; left: 46px; top: 419px;
    font-size: 18px; font-weight: 600; white-space: nowrap; letter-spacing: 0.8px;
  }
  .website__domain { font-size: 23px; font-weight: 700; }
  .mobile {
    position: absolute; left: 506px; top: 37px;
    color: var(--white); font-size: 19px; letter-spacing: 0.8px; white-space: nowrap;
  }
</style>
</head>
<body>
<main class="sheet">

  <section class="card card--front" aria-label="Card front">
    <svg class="card__bands" viewBox="0 0 820 466" aria-hidden="true">
      <defs>
        <radialGradient id="leafGlowFront" cx="0.55" cy="0.45" r="0.6">
          <stop offset="0" stop-color="#f7a449"/>
          <stop offset="0.5" stop-color="#3f8fd0"/>
          <stop offset="1" stop-color="#b5d33c"/>
        </radialGradient>
      </defs>
      <path class="band--sun" d="M262,0 Q650,80 712,466 L820,466 L820,0 Z"/>
      <path class="band--slate" d="M288,0 Q748,110 802,466 L820,466 L820,0 Z"/>
      <rect role="img" aria-label="Cluster of colourful leaf shapes" x="686" y="0" width="134" height="172" rx="40" fill="url(#leafGlowFront)" opacity="0.85"/>
    </svg>
    <div class="brand">
      <div class="brand__mark"></div>
      <div class="brand__name">VISTALUME WORKS</div>
      <div class="brand__rule"></div>
      <div class="brand__tagline">FINE ART PHOTOGRAPHY</div>
    </div>
  </section>

  <section class="card card--back" aria-label="Card back">
    <svg class="card__bands" viewBox="0 0 820 466" aria-hidden="true">
      <defs>
        <radialGradient id="leafGlowBack" cx="0.55" cy="0.45" r="0.6">
          <stop offset="0" stop-color="#f7a449"/>
          <stop offset="0.5" stop-color="#3f8fd0"/>
          <stop offset="1" stop-color="#b5d33c"/>
        </radialGradient>
      </defs>
      <path class="band--sun" d="M262,0 Q650,80 708,466 L820,466 L820,0 Z"/>
      <path class="band--slate" d="M288,0 Q748,110 800,466 L820,466 L820,0 Z"/>
      <rect role="img" aria-label="Cluster of colourful leaf shapes" x="684" y="0" width="136" height="176" rx="40" fill="url(#leafGlowBack)" opacity="0.85"/>
    </svg>
    <div class="mobile">M : 0417 539 662</div>
    <div class="brand">
      <div class="brand__mark"></div>
      <div class="brand__name">VISTALUME WORKS</div>
      <div class="brand__rule"></div>
      <div class="brand__tagline">FINE ART PHOTOGRAPHY</div>
    </div>
    <ul class="contact">
      <li class="contact__item"><span class="contact__key">E</span> : sales@vistalumeworks.com.au</li>
      <li class="contact__item"><span class="contact__key">T</span> : chirpline.com/vistalumeworks</li>
      <li class="contact__item"><span class="contact__key">F</span> : friendnook.com/vistalumeworks</li>
    </ul>
    <div class="website">www.<span class="website__domain">VISTALUMEWORKS</span>.com.au</div>
  </section>

</main>
</body>
</html>
```